Dwelvano - "Where Pest Control is Free for Life..." Please see pitch deck...

Project goal, that this is a reusable template, not a one-off card
Brand and design direction, follow the logo, use the brand palette (with a color swatch table), typography and layout guidance
The John Doe placeholder content as a clean field-by-field table (name, title, company, address, office, cell, fax, email, dwelvano.com)
Print specs, 3.5 × 2 in trim, 0.125 in bleed, 300 DPI, CMYK, crop marks
Deliverables, layered editable PSD (your primary ask) plus vector .AI/.EPS and a press-ready PDF/X-1a, with fonts packaged
What you'll provide (logo, colors, fonts)
Process and sign-off, concept first, then full file package on approval.
Populate every field with this John Doe placeholder data so we can see the layout fully built out. We will replace it per person.
Name John Doe
Title Title / Position
Company Dwelvano
Address 123 Main Street, Suite 100, Tallahassee, FL 32301
Office (850) 555-0100
Cell (850) 555-0123
Fax (850) 555-0199
Email johndoe@dwelvano.com
Website dwelvano.com

We need the working, editable source files so we can update them ourselves, plus a ready-to-print export:
1. Photoshop (.PSD) — fully layered and editable, with each contact field on its own labeled text layer. This is the primary requested format.
2. Vector source — the press-standard editable format, Adobe Illustrator (.AI) and/or .EPS, since vector is preferred for crisp text and logos at print.
3. Print-ready PDF — press-quality (PDF/X-1a), CMYK, with bleed and crop marks, both sides.
4. Packaged fonts and links — include or list all fonts used, and package any linked assets so the files open correctly on our end.

Why both PSD and vector
The PSD covers our request directly and is easy for us to edit. Vector (.AI/.EPS) is what most commercial printers actually prefer for type and logos because it stays razor-sharp at any size. Providing both keeps us flexible no matter which printer we use. Have fun and keep it modern and cool the designer of the logo did a great job, see what you can do.

```html
<!DOCTYPE html>
<html lang="en">
<head>
<meta charset="UTF-8">
<title>Dwelvano Business Card</title>
<link href="https://fonts.googleapis.com/css2?family=Montserrat:wght@400;500;700;800&display=swap" rel="stylesheet">
<style>
  :root {
    --navy: #0f1729;
    --navy-raised: #1a2540;
    --teal: #1fb3c4;
    --ink: #141a2a;
    --paper: #ffffff;
    --stage: #3b3b3d;
  }
  * { box-sizing: border-box; margin: 0; padding: 0; }
  html, body { width: 1200px; height: 875px; overflow: hidden; }
  body {
    background: var(--stage);
    font-family: "Montserrat", sans-serif;
    display: flex;
    align-items: center;
    justify-content: center;
    gap: 40px;
  }
  .card {
    width: 540px;
    height: 309px;
    border-radius: 22px;
    border: 3px solid var(--teal);
    position: relative;
    overflow: hidden;
    flex: none;
  }
  .card--back {
    background: var(--navy);
    display: flex;
    align-items: center;
    justify-content: center;
    padding: 0 40px;
  }
  .back-wordmark {
    font-weight: 800;
    font-size: 50px;
    letter-spacing: -0.5px;
    color: var(--navy-raised);
    white-space: nowrap;
  }
  .card--front {
    background: var(--paper);
    display: flex;
    align-items: center;
    padding: 0 28px 0 30px;
  }
  .front-wordmark {
    font-weight: 800;
    font-size: 36px;
    letter-spacing: -0.5px;
    color: var(--ink);
    white-space: nowrap;
    flex: none;
    margin-top: 48px;
  }
  .divider {
    width: 2px;
    height: 178px;
    background: var(--teal);
    margin: 0 22px 0 24px;
    flex: none;
  }
  .contact { color: var(--ink); white-space: nowrap; }
  .contact__name {
    font-weight: 700;
    font-size: 24px;
    color: var(--teal);
    line-height: 1.1;
  }
  .contact__title { font-size: 11.5px; margin-bottom: 12px; }
  .contact__address { font-size: 11.5px; line-height: 1.45; margin-bottom: 10px; }
  .contact__list { list-style: none; font-size: 11.5px; line-height: 1.55; }
  .contact__list li { display: flex; align-items: center; gap: 7px; }
  .contact__list svg { width: 11px; height: 11px; fill: var(--teal); flex: none; }
</style>
</head>
<body>
  <section class="card card--back" aria-label="Card back">
    <span class="back-wordmark">Dwelvano.com</span>
  </section>

  <section class="card card--front" aria-label="Card front">
    <div class="front-wordmark">Dwelvano</div>
    <div class="divider"></div>
    <div class="contact">
      <p class="contact__name">John Doe</p>
      <p class="contact__title">Title / Position</p>
      <p class="contact__address">123 Main Street, Suite 100,<br>Tallahassee, FL 32301</p>
      <ul class="contact__list">
        <li><svg viewBox="0 0 12 12"><path d="M1 4c0-2 2-3 5-3s5 1 5 3l-2 1-1-2H4L3 5 1 4zm2 2h6l1 5H2l1-5z"/></svg>(850) 555-0100</li>
        <li><svg viewBox="0 0 12 12"><path d="M3 0h6v12H3zM4 1.5v8h4v-8z"/></svg>(850) 555-0123</li>
        <li><svg viewBox="0 0 12 12"><path d="M3 0h6v4H3zM1 4h10v5H9v3H3V9H1zm3 4v3h4V8z"/></svg>(850) 555-0199</li>
        <li><svg viewBox="0 0 12 12"><path d="M0 2h12v8H0zm1 1v.5l5 3.5 5-3.5V3z"/></svg>johndoe@dwelvano.com</li>
        <li><svg viewBox="0 0 12 12"><circle cx="6" cy="6" r="5.5"/></svg>dwelvano.com</li>
      </ul>
    </div>
  </section>
</body>
</html>
```